Modern card design needed for building development company

We are looking for a sharp modern new look for our business cards.
We are a New Zealand based company called TKR Ventures NZ LTD that specialises in subdividing large sections, housing and commercial buildings.
We have attached a photo of the current logo and would like to see it improved somehow as it looks a bit dated.
We are open to any colours.

Target Market(s)

Investors, Property buyers

Industry/Entity Type

Investment

Contact Information for Business Card

TKR VENTURES NZ LTD
www.tkrventuresnz.co.nz

Damon Whitcombe
Phone +64 21 938 104
Email dpwhitcombe@korumail.co.nz

Font styles to use
Serif
Sans Serif

Colors
0792cd
33a6d7
85cae6
6b449b
886aae
f04a50
ec1f27
f37122
f68d4d

Requirements
Must have
• Please try and make the logo more modern or if you have a similar one we would like to see it.

```html
<!DOCTYPE html>
<html lang="en">
<head>
<meta charset="utf-8">
<title>TKR Ventures NZ LTD – Business Card</title>
<link rel="stylesheet" href="https://fonts.googleapis.com/css2?family=Cinzel:wght@400&family=PT+Sans:wght@400;700&display=swap">
<style>
  :root {
    --backdrop: #000000;
    --card-light: #f3f3f3;
    --brand-blue: #1046c4;
    --brand-blue-deep: #0f3fb3;
    --ink: #333333;
    --ink-soft: #555555;
    --white: #ffffff;
  }
  * { margin: 0; padding: 0; box-sizing: border-box; }
  html, body {
    width: 1200px; height: 900px; overflow: hidden;
    background: var(--backdrop);
  }
  .canvas { position: relative; width: 1200px; height: 900px; }

  .card {
    position: absolute; top: 200px;
    width: 310px; height: 502px;
  }
  .card-front {
    left: 265px;
    background: var(--card-light);
    border-radius: 46px 0 46px 0;
  }
  .card-back {
    left: 641px; width: 309px;
    background: var(--brand-blue);
    border-radius: 0 46px 0 46px;
  }

  /* Company name lockup */
  .wordmark {
    position: absolute; left: 0; right: 0;
    text-align: center;
    font-family: "Cinzel", Georgia, serif;
    font-weight: 400;
  }
  .wordmark-mark {
    display: block; width: 34px; height: 34px;
    margin: 0 auto 18px;
    background: var(--brand-blue);
  }
  .wordmark-name { display: block; line-height: 1; }
  .wordmark-sub {
    display: flex; align-items: center; justify-content: center;
    gap: 8px; line-height: 1;
  }
  .wordmark-sub::before, .wordmark-sub::after {
    content: ""; height: 1px; background: currentColor;
  }

  .card-front .wordmark { top: 82px; color: var(--ink); }
  .card-front .wordmark-name { font-size: 28px; letter-spacing: 0.5px; }
  .card-front .wordmark-sub { font-size: 18px; margin-top: 8px; }
  .card-front .wordmark-sub::before,
  .card-front .wordmark-sub::after { width: 58px; }

  .card-back .wordmark { top: 392px; color: var(--white); }
  .card-back .wordmark-name { font-size: 31px; letter-spacing: 0.5px; }
  .card-back .wordmark-sub { font-size: 22px; margin-top: 10px; }
  .card-back .wordmark-sub::before,
  .card-back .wordmark-sub::after { width: 84px; }

  /* Person & contact */
  .person-name {
    position: absolute; top: 374px; left: 0; right: 0;
    text-align: center;
    font-family: "PT Sans", Arial, sans-serif;
    font-weight: 700; font-size: 18px;
    color: var(--brand-blue);
  }
  .contact-list {
    position: absolute; left: 23px; top: 422px;
    list-style: none;
    font-family: "PT Sans", Arial, sans-serif;
    font-size: 13.5px; color: var(--ink-soft);
  }
  .contact-item {
    display: flex; align-items: center; gap: 8px;
    height: 21px;
  }
  .contact-icon { width: 11px; height: 11px; fill: var(--brand-blue); flex: none; }
</style>
</head>
<body>
<div class="canvas">

  <section class="card card-front">
    <div class="wordmark">
      <span class="wordmark-mark"></span>
      <span class="wordmark-name">TKR Ventures</span>
      <span class="wordmark-sub">NZ LTD</span>
    </div>

    <p class="person-name">Damon Whitcombe</p>

    <ul class="contact-list">
      <li class="contact-item">
        <svg class="contact-icon" viewBox="0 0 24 24" aria-hidden="true"><path d="M6.6 10.8a15.2 15.2 0 0 0 6.6 6.6l2.2-2.2a1 1 0 0 1 1-.25 11.4 11.4 0 0 0 3.6.57 1 1 0 0 1 1 1V20a1 1 0 0 1-1 1A17 17 0 0 1 3 4a1 1 0 0 1 1-1h3.5a1 1 0 0 1 1 1c0 1.25.2 2.45.57 3.57a1 1 0 0 1-.25 1z"/></svg>
        <span>+64 21 938 104</span>
      </li>
      <li class="contact-item">
        <svg class="contact-icon" viewBox="0 0 24 24" aria-hidden="true"><path d="M2 5h20v14H2z" /><path d="M2 5l10 8 10-8" fill="none" stroke="#f3f3f3" stroke-width="2"/></svg>
        <span>dpwhitcombe@korumail.co.nz</span>
      </li>
      <li class="contact-item">
        <svg class="contact-icon" viewBox="0 0 24 24" aria-hidden="true"><circle cx="12" cy="12" r="11"/><path d="M1 12h22M12 1c4 4 4 18 0 22M12 1c-4 4-4 18 0 22" fill="none" stroke="#f3f3f3" stroke-width="1.6"/></svg>
        <span>www.tkrventuresnz.co.nz</span>
      </li>
    </ul>
  </section>

  <section class="card card-back">
    <div class="wordmark">
      <span class="wordmark-name">TKR VENTURES</span>
      <span class="wordmark-sub">NZ LTD</span>
    </div>
  </section>

</div>
</body>
</html>
```